Bright Harbor Web Design & Marketing

Will award a 2nd place prize of $100.00 if someone can come up with a logo to match this design!
Updates

Okay, I'm really looking to see some better designs here. What do you think will bring the best designs out? Please remember with all future submissions I'm looking for a cartoon style / illustrator style website. I'm not sure what the technical term is for it, so I uploaded some images in the brief.

Target Market(s)

Small Business Owners

Industry/Entity Type

Marketing

Logo Text

BrightHarbor.com

Number of Pages Required

1 page

Colors

Designer to choose colors to be used in the design.

Requirements
Must have
• Logo should say BrightHarbor.com I would like more than just a text logo. I want some sort of cool custom graphic / icon with it that will look nice on shirts/hats/etc

```html
<!DOCTYPE html>
<html lang="en">
<head>
<meta charset="utf-8">
<title>Bright Harbor Web Design &amp; Marketing</title>
<link rel="stylesheet" href="https://fonts.googleapis.com/css2?family=Cinzel:wght@400;700&family=Open+Sans:wght@400;600;700&family=Tinos:wght@400;700&display=swap">
<style>
:root{
  --blue:#1d6fb8;
  --blue-dark:#155a96;
  --orange:#f58a3c;
  --orange-deep:#e8731f;
  --ink:#222;
  --muted:#555;
  --night:#1e282e;
  --cream:#f7f4ea;
  --sky:#e0eaf5;
  --footer:#2a2e33;
  --gray-btn:#555a5e;
  --white:#fff;
}
*{box-sizing:border-box;margin:0;padding:0}
html,body{width:1200px;height:4455px;overflow:hidden}
body{position:relative;font-family:'Open Sans',sans-serif;color:var(--ink);background:var(--white)}
.abs{position:absolute}
.section-title{position:absolute;left:0;width:1200px;text-align:center;font-family:'Cinzel',serif;font-size:32px;font-weight:400;letter-spacing:2px;color:var(--ink)}
.lead{position:absolute;left:110px;width:980px;text-align:center;font-family:'Tinos',serif;font-size:12.5px;line-height:19px;color:var(--muted)}
.placeholder{position:absolute}

/* header */
.site-header{position:absolute;top:0;left:0;width:1200px;height:89px;background:var(--white)}
.brand{position:absolute;left:150px;top:18px;display:flex;align-items:center;gap:12px}
.brand-dot{width:48px;height:48px;border-radius:50%;background:var(--orange)}
.brand-name{font-family:'Tinos',serif;font-size:36px;font-weight:700;color:var(--blue)}
.phone{position:absolute;left:878px;top:28px;display:flex;align-items:center;gap:10px;font-size:26px;color:var(--blue-dark);font-weight:600}
.main-nav{position:absolute;top:89px;left:0;width:1200px;height:30px;background:var(--blue)}
.main-nav a{position:absolute;top:0;height:30px;line-height:30px;text-align:center;color:var(--white);font-family:'Cinzel',serif;font-size:14px;font-weight:700;text-decoration:none;letter-spacing:1px}
.main-nav a.active{background:var(--orange)}

/* hero */
.hero{position:absolute;top:119px;left:0;width:1200px;height:495px;background:var(--orange)}
.hero h1{position:absolute;top:48px;left:0;width:1200px;text-align:center;font-family:'Tinos',serif;font-weight:400;font-size:28px;color:var(--white);letter-spacing:.5px}
.btn-call{position:absolute;display:flex;align-items:center;justify-content:center;gap:8px;height:44px;width:196px;color:var(--white);font-size:20px;font-family:'Tinos',serif}
.hero .btn-call{left:502px;top:92px;background:var(--blue)}
.slider-arrow{position:absolute;top:236px;width:24px;height:22px;background:#ddd;display:flex;align-items:center;justify-content:center}

/* about */
.about-title span{color:var(--orange)}
.video{left:352px;top:817px;width:496px;height:328px;background:linear-gradient(#3b3d40,#6c6f73);border-radius:12px}
.about .btn-call{left:502px;top:1138px;background:var(--gray-btn)}

/* services */
.services{position:absolute;top:1232px;left:0;width:1200px;height:758px;background:linear-gradient(#1a2328,#26343b)}
.services .section-title{top:42px;color:var(--white)}
.services .lead{top:92px;color:#d8dde0}

/* plans */
.plan{position:absolute;top:2132px;width:208px;height:481px;background:var(--white);border-top:5px solid var(--blue);box-shadow:0 2px 8px rgba(0,0,0,.18);text-align:center}
.plan-icon{width:46px;height:46px;border-radius:50%;margin:40px auto 0;display:flex;align-items:center;justify-content:center;border:3px solid #cfd8e3}
.plan-name{margin-top:22px;font-size:17px;font-weight:600;color:#333}
.plan-from{margin-top:30px;font-family:'Tinos',serif;font-size:12px;color:#666}
.plan-price{font-family:'Tinos',serif;font-size:38px;color:#333}
.plan-price small{font-size:16px;vertical-align:super}
.plan-price .cur{font-size:18px;vertical-align:super}
.plan-basic .plan-price{color:var(--orange-deep)}
.plan-list{list-style:none;margin:26px 0 0 28px;text-align:left;font-family:'Tinos',serif;font-size:12px;color:#555}
.plan-list li{height:28px}
.plan-list li::before{content:"›";margin-right:8px;color:#999}
.plan-btn{display:block;width:116px;height:28px;line-height:28px;margin:24px auto 0;background:var(--gray-btn);color:var(--white);font-size:13px}
.plan-basic .plan-btn{background:var(--orange-deep)}
.plan-more{margin-top:8px;font-size:11px;color:#333}

/* clients */
.clients{position:absolute;top:2643px;left:0;width:1200px;height:270px;background:var(--cream)}
.client{position:absolute;top:167px;width:104px;height:50px;background:var(--white);display:flex;align-items:center;justify-content:center;gap:6px;font-size:14px;font-weight:600;color:#333}
.client i{width:10px;height:10px;border-radius:50%;background:#333;display:block}

/* why */
.why{position:absolute;top:2913px;left:0;width:1200px;height:540px;background:var(--sky)}
.why-item{position:absolute;width:250px;font-family:'Tinos',serif;font-size:12px;line-height:16px;color:#444}
.why-item b{display:block;font-family:'Open Sans',sans-serif;font-size:13px;color:var(--blue-dark);font-weight:600}
.why-icon{position:absolute;width:44px;height:44px;border-radius:50%;border:3px solid #fff;display:flex;align-items:center;justify-content:center}
.why-emblem{left:555px;top:190px;width:90px;height:90px;border-radius:20px;background:var(--blue);transform:rotate(45deg)}

/* team */
.member{position:absolute;top:3600px;width:430px;height:112px}
.member-photo{position:absolute;left:0;top:0;width:70px;height:70px;background:linear-gradient(#c9ccd0,#8f959b)}
.member-head{position:absolute;left:80px;top:6px;right:0;height:54px;border:1px solid #ddd;border-left:none;padding:8px 12px}
.member-head b{display:block;font-size:13px;color:#222}
.member-head span{font-size:12px;color:var(--blue)}
.member p{position:absolute;left:0;top:82px;width:430px;font-family:'Tinos',serif;font-size:11.5px;line-height:15px;color:#555}
.team-arrow{position:absolute;top:3640px;font-size:22px;color:#999}

/* inquiry */
.field{position:absolute;font-size:11px;color:#555;border-bottom:1px solid #ccc;height:36px;padding-top:2px}
.submit{position:absolute;left:493px;top:4096px;width:84px;height:26px;background:var(--blue);color:var(--white);font-size:12px;display:flex;align-items:center;justify-content:center}

/* footer */
.site-footer{position:absolute;top:4173px;left:0;width:1200px;height:252px;background:linear-gradient(#30353b,#22262a)}
.foot-col{position:absolute;top:40px;color:#ddd;font-family:'Tinos',serif;font-size:12px;line-height:18px}
.foot-col h4{font-family:'Tinos',serif;font-weight:400;font-size:15px;color:#fff;margin-bottom:12px}
.foot-col h4 span{color:var(--orange)}
.foot-col ul{list-style:none}
.foot-col li::before{content:"› ";}
.news-input{width:220px;height:24px;background:#fff;color:#666;padding:4px 6px;font-size:11px;margin-top:12px}
.news-btn{display:inline-block;margin-top:10px;padding:3px 10px;background:var(--blue);color:#fff;font-size:13px}
.copyright{position:absolute;top:4425px;left:0;width:1200px;height:30px;background:var(--blue);color:#fff;font-size:11px;line-height:30px;padding:0 150px;display:flex;justify-content:space-between}
</style>
</head>
<body>

<header class="site-header">
  <div class="brand"><span class="brand-dot"></span><span class="brand-name">BrightHarbor.com</span></div>
  <div class="phone">
    <svg width="30" height="30" viewBox="0 0 30 30"><circle cx="15" cy="15" r="13" fill="none" stroke="#155a96" stroke-width="2"/><path d="M10 8c1-1 2-1 3 1l1 3c0 1-1 2-1 2 1 2 2 3 4 4 0 0 1-1 2-1l3 1c2 1 2 2 1 3-3 3-7 1-10-2s-5-8-3-11z" fill="#155a96"/></svg>
    555-014-2290
  </div>
</header>

<nav class="main-nav">
  <a class="active" href="#" style="left:140px;width:120px">Home</a>
  <a href="#" style="left:300px;width:200px">Services &amp; Pricing</a>
  <a href="#" style="left:560px;width:140px">Our Team</a>
  <a href="#" style="left:740px;width:140px">Clients</a>
  <a href="#" style="left:920px;width:150px">Contact Us</a>
</nav>

<section class="hero">
  <h1>The Design &amp; Marketing Team That Always Puts Trust &amp; Loyalty Before Profits</h1>
  <div class="btn-call"><svg width="16" height="16" viewBox="0 0 16 16"><path d="M3 1c1-1 2 0 3 2l1 2-2 2c1 2 2 3 4 4l2-2 2 1c2 1 2 2 1 3-2 2-6 1-9-2S1 3 3 1z" fill="#fff"/></svg>Call Us Today</div>
  <div class="placeholder" role="img" aria-label="Cartoon mascot illustration" style="left:420px;top:150px;width:360px;height:320px;background:radial-gradient(circle at 50% 40%,#3a3a3a,#e07b30 75%);opacity:.85;border-radius:40% 40% 20% 20%"></div>
  <div class="slider-arrow" style="left:6px"><svg width="8" height="10"><path d="M7 0L0 5l7 5z" fill="#333"/></svg></div>
  <div class="slider-arrow" style="left:1170px"><svg width="8" height="10"><path d="M1 0l7 5-7 5z" fill="#333"/></svg></div>
  <svg class="abs" style="left:0;top:470px" width="1200" height="26" viewBox="0 0 1200 26"><path d="M0 14q60-12 120 0t120 0 120 0 120 0 120 0 120 0 120 0 120 0 120 0 120 0V26H0z" fill="#fff"/></svg>
</section>

<section class="about">
  <h2 class="section-title about-title" style="top:645px">About <span>BrightHarbor.com</span></h2>
  <p class="lead" style="top:700px">We believe that honesty and integrity come before personal profits. We are a family owned and operated company. Our parents raised us to take care of each other and that's exactly what we've done. We treat each of our clients with the same loyalty and respect that we give each other.<br>We are not looking to have hundreds and hundreds of clients. We are looking to expand our family with a handful of like-minded individuals. Companies who take pride in their work and their customers. We want to build mutually beneficial, lucrative, and long term partnerships.</p>
  <div class="placeholder video" role="img" aria-label="Laptop showing company introduction video"></div>
  <svg class="abs" style="left:574px;top:955px" width="52" height="52" viewBox="0 0 52 52"><circle cx="26" cy="26" r="25" fill="#fff" opacity=".9"/><path d="M20 15l18 11-18 11z" fill="#333"/></svg>
  <div class="btn-call"><svg width="16" height="16" viewBox="0 0 16 16"><path d="M3 1c1-1 2 0 3 2l1 2-2 2c1 2 2 3 4 4l2-2 2 1c2 1 2 2 1 3-2 2-6 1-9-2S1 3 3 1z" fill="#fff"/></svg>Call Us Today</div>
</section>

<section class="services" role="img" aria-label="Dark cartoon city scene behind the services diagram">
  <svg class="abs" style="left:0;top:-8px" width="1200" height="30" viewBox="0 0 1200 30"><path d="M0 0h1200v10q-100 12-200 0t-200 0-200 0-200 0-200 0-200 0z" fill="#fff"/></svg>
  <h2 class="section-title">Services We Provide</h2>
  <p class="lead">Lorem ipsum dolor sit amet, consectetuer adipiscing elit, sed diam nonummy nibh euismod tincidunt ut laoreet dolore magna aliquam erat volutpat. Ut wisi enim ad minim veniam, quis nostrud exerci.</p>
  <svg class="abs" style="left:0;top:0" width="1200" height="758" viewBox="0 1232 1200 758" font-family="Open Sans, sans-serif">
    <circle cx="600" cy="1625" r="205" fill="none" stroke="#3e6f7d" stroke-width="2" stroke-dasharray="4 6"/>
    <g stroke="#3e6f7d" stroke-width="2">
      <line x1="600" y1="1625" x2="668" y2="1426"/><line x1="600" y1="1625" x2="757" y2="1530"/><line x1="600" y1="1625" x2="802" y2="1648"/>
      <line x1="600" y1="1625" x2="728" y2="1773"/><line x1="600" y1="1625" x2="609" y2="1841"/><line x1="600" y1="1625" x2="451" y2="1797"/>
      <line x1="600" y1="1625" x2="395" y2="1678"/><line x1="600" y1="1625" x2="416" y2="1544"/><line x1="600" y1="1625" x2="535" y2="1440"/>
    </g>
    <circle cx="600" cy="1625" r="72" fill="#f4f4f4"/>
    <text x="600" y="1630" text-anchor="middle" font-size="13" font-weight="700" fill="#1d6fb8">BrightHarbor</text>
    <g font-size="12" font-weight="700" fill="#fff" text-anchor="middle">
      <circle cx="668" cy="1426" r="30" fill="#22b5e0"/><circle cx="688" cy="1416" r="10" fill="#fff"/><text x="688" y="1420" fill="#22b5e0">1</text>
      <circle cx="757" cy="1530" r="30" fill="#8cc63f"/><circle cx="777" cy="1545" r="10" fill="#fff"/><text x="777" y="1549" fill="#8cc63f">2</text>
      <circle cx="802" cy="1648" r="30" fill="#9b3fc1"/><circle cx="788" cy="1672" r="10" fill="#fff"/><text x="788" y="1676" fill="#9b3fc1">3</text>
      <circle cx="728" cy="1773" r="30" fill="#e8542a"/><circle cx="752" cy="1760" r="10" fill="#fff"/><text x="752" y="1764" fill="#e8542a">4</text>
      <circle cx="609" cy="1841" r="30" fill="#1f8fe0"/><circle cx="635" cy="1830" r="10" fill="#fff"/><text x="635" y="1834" fill="#1f8fe0">5</text>
      <circle cx="451" cy="1797" r="30" fill="#2ab0c0"/><circle cx="475" cy="1815" r="10" fill="#fff"/><text x="475" y="1819" fill="#2ab0c0">6</text>
      <circle cx="395" cy="1678" r="30" fill="#b9cf25"/><circle cx="418" cy="1696" r="10" fill="#fff"/><text x="418" y="1700" fill="#9aad18">7</text>
      <circle cx="416" cy="1544" r="30" fill="#2a9fb0"/><circle cx="392" cy="1560" r="10" fill="#fff"/><text x="392" y="1564" fill="#2a9fb0">8</text>
      <circle cx="535" cy="1440" r="30" fill="#f39a1e"/><circle cx="512" cy="1430" r="10" fill="#fff"/><text x="512" y="1434" fill="#f39a1e">9</text>
    </g>
    <g font-size="12">
      <text x="730" y="1400" fill="#22b5e0">Website Design &amp; Management</text>
      <text x="835" y="1503" fill="#8cc63f">Logo Design &amp; Branding Materials</text>
      <text x="860" y="1610" fill="#b77fe0">Video Production &amp; Commercials</text>
      <text x="800" y="1775" fill="#f0784a">Local Seo Management</text>
      <text x="665" y="1870" fill="#1f8fe0">Search Engine Optimization</text>
      <text x="250" y="1780" fill="#2ab0c0">Social Media Marketing</text>
      <text x="135" y="1655" fill="#b9cf25">Marketing Material &amp; Print Design</text>
      <text x="200" y="1520" fill="#2a9fb0">Outsourcing</text>
      <text x="340" y="1396" fill="#f39a1e">Consulting Service</text>
    </g>
    <g font-size="10" fill="#e4e8ea">
      <text x="730" y="1415">Duis autem vel eum iriure</text><text x="730" y="1428">dolor in hendrerit in vulputate</text><text x="730" y="1441">velit consequat.</text>
      <text x="835" y="1518">Duis autem vel eum iriure</text><text x="835" y="1531">dolor in hendrerit in vulputate</text><text x="835" y="1544">velit consequat.</text>
      <text x="860" y="1625">Duis autem vel eum iriure</text><text x="860" y="1638">dolor in hendrerit in vulputate.</text>
      <text x="800" y="1790">Duis autem vel eum iriure</text><text x="800" y="1803">dolor in hendrerit in vulputate</text><text x="800" y="1816">velit consequat.</text>
      <text x="665" y="1885">Duis autem vel eum iriure</text><text x="665" y="1898">dolor in hendrerit in vulputate.</text>
      <text x="250" y="1795">Duis autem vel eum iriure</text><text x="250" y="1808">dolor in hendrerit in vulputate</text><text x="250" y="1821">velit consequat.</text>
      <text x="135" y="1670">Duis autem vel eum iriure</text><text x="135" y="1683">dolor in hendrerit in vulputate</text><text x="135" y="1696">velit consequat.</text>
      <text x="200" y="1535">Duis autem vel eum iriure</text><text x="200" y="1548">dolor in hendrerit in vulputate</text><text x="200" y="1561">velit consequat.</text>
      <text x="340" y="1411">Duis autem vel eum iriure</text><text x="340" y="1424">dolor in hendrerit in vulputate</text><text x="340" y="1437">velit consequat.</text>
    </g>
  </svg>
</section>

<section class="plans">
  <h2 class="section-title" style="top:2042px">Select Your Plan</h2>
  <div class="placeholder" role="img" aria-label="Wooden floor and wall backdrop" style="left:0;top:2530px;width:1200px;height:113px;background:linear-gradient(#e9e6e0 0,#e9e6e0 20%,#c98a55 21%,#a8683a)"></div>
  <div class="plan plan-basic" style="left:157px">
    <div class="plan-icon"><svg width="22" height="22"><circle cx="11" cy="11" r="9" fill="#1d6fb8"/></svg></div>
    <div class="plan-name">Basic Plan</div><div class="plan-from">Starting from</div>
    <div class="plan-price"><span class="cur">$</span>52<small>.95</small></div>
    <ul class="plan-list"><li>Lorem Ipsum Dolar Sipsum</li><li>Lorem Ipsum Dolar</li><li>Lorem Ipsum Dolar Sipsum</li><li>Lorem Ipsum Dolar</li></ul>
    <span class="plan-btn">Get Started →</span><div class="plan-more">More Information ▪</div>
  </div>
  <div class="plan" style="left:395px;top:2122px">
    <div class="plan-icon"><svg width="22" height="22"><rect x="3" y="5" width="16" height="12" fill="#555"/></svg></div>
    <div class="plan-name">Standard Plan</div><div class="plan-from">Starting from</div>
    <div class="plan-price"><span class="cur">$</span>114<small>.00</small></div>
    <ul class="plan-list"><li>Lorem Ipsum Dolar Sipsum</li><li>Lorem Ipsum Dolar</li><li>Lorem Ipsum Dolar Sipsum</li><li>Lorem Ipsum Dolar</li></ul>
    <span class="plan-btn">Get Started →</span><div class="plan-more">More Information ▪</div>
  </div>
  <div class="plan" style="left:633px">
    <div class="plan-icon"><svg width="22" height="22"><circle cx="10" cy="10" r="7" fill="none" stroke="#e8a020" stroke-width="3"/><line x1="15" y1="15" x2="20" y2="20" stroke="#e8a020" stroke-width="3"/></svg></div>
    <div class="plan-name">Gold Plan</div><div class="plan-from">Starting from</div>
    <div class="plan-price"><span class="cur">$</span>200<small>.95</small></div>
    <ul class="plan-list"><li>Lorem Ipsum Dolar Sipsum</li><li>Lorem Ipsum Dolar</li><li>Lorem Ipsum Dolar Sipsum</li><li>Lorem Ipsum Dolar</li></ul>
    <span class="plan-btn">Get Started →</span><div class="plan-more">More Information ▪</div>
  </div>
  <div class="plan" style="left:870px">
    <div class="plan-icon"><svg width="22" height="22"><circle cx="10" cy="10" r="7" fill="none" stroke="#888" stroke-width="3"/><line x1="15" y1="15" x2="20" y2="20" stroke="#888" stroke-width="3"/></svg></div>
    <div class="plan-name">Platinum Plan</div><div class="plan-from">Starting from</div>
    <div class="plan-price"><span class="cur">$</span>490<small>.00</small></div>
    <ul class="plan-list"><li>Lorem Ipsum Dolar Sipsum</li><li>Lorem Ipsum Dolar</li><li>Lorem Ipsum Dolar Sipsum</li><li>Lorem Ipsum Dolar</li></ul>
    <span class="plan-btn">Get Started →</span><div class="plan-more">More Information ▪</div>
  </div>
</section>

<section class="clients">
  <h2 class="section-title" style="top:45px">Our Clients</h2>
  <p class="lead" style="top:96px">Lorem ipsum dolor sit amet, consectetuer adipiscing elit, sed diam nonummy nibh euismod tincidunt ut laoreet dolore magna aliquam erat volutpat. Ut wisi enim ad minim veniam, quis nostrud exerci.</p>
  <span class="abs" style="left:112px;top:178px;color:#999;font-size:22px">‹</span>
  <div class="client" style="left:148px"><i></i>Larkfield</div>
  <div class="client" style="left:262px">Norvale</div>
  <div class="client" style="left:376px">Norvale</div>
  <div class="client" style="left:490px">Keystep</div>
  <div class="client" style="left:604px"><i></i>Larkfield</div>
  <div class="client" style="left:718px"><i></i>Brightwell</div>
  <div class="client" style="left:832px">Arcline</div>
  <div class="client" style="left:946px">Arcline</div>
  <span class="abs" style="left:1074px;top:178px;color:#999;font-size:22px">›</span>
</section>

<section class="why">
  <svg class="abs" style="left:0;top:-3px" width="1200" height="24" viewBox="0 0 1200 24"><path d="M0 0h1200v6q-75 14-150 0t-150 0-150 0-150 0-150 0-150 0-150 0-150 0z" fill="#f7f4ea"/></svg>
  <h2 class="section-title" style="top:62px">Why Choose Us</h2>
  <p class="lead" style="top:112px">Lorem ipsum dolor sit amet, consectetuer adipiscing elit, sed diam nonummy nibh euismod tincidunt ut laoreet dolore magna aliquam erat volutpat. Ut wisi enim ad minim veniam, quis nostrud exerci.</p>
  <svg class="abs" style="left:0;top:0" width="1200" height="540"><path d="M425 250 A180 180 0 0 0 775 250" fill="none" stroke="#9bb8d6" stroke-width="2" stroke-dasharray="4 5"/></svg>
  <div class="placeholder why-emblem" role="img" aria-label="Company emblem badge"></div>
  <div class="why-icon" style="left:403px;top:228px;background:var(--orange)"><svg width="18" height="18"><circle cx="9" cy="9" r="6" fill="#fff"/></svg></div>
  <div class="why-item" style="left:143px;top:222px;text-align:right"><b style="color:var(--orange-deep)">100% Risk Free Investment</b>Lorem ipsum dolor sit amet, consectetuer adipiscing elit, sed diam.</div>
  <div class="why-icon" style="left:753px;top:223px;background:var(--blue)"><svg width="18" height="18"><rect x="2" y="4" width="14" height="10" fill="#fff"/></svg></div>
  <div class="why-item" style="left:808px;top:218px"><b>Multiple Payment Options Available</b>Lorem ipsum dolor sit amet, consectetuer adipiscing elit, sed diam.</div>
  <div class="why-icon" style="left:460px;top:335px;background:var(--blue)"><svg width="18" height="18"><rect x="3" y="3" width="12" height="12" fill="#fff"/></svg></div>
  <div class="why-item" style="left:195px;top:333px;text-align:right"><b>Customer Loyalty Program</b>Lorem ipsum dolor sit amet, consectetuer adipiscing elit, sed diam.</div>
  <div class="why-icon" style="left:697px;top:335px;background:var(--blue)"><svg width="18" height="18"><circle cx="9" cy="7" r="4" fill="#fff"/><rect x="3" y="12" width="12" height="5" fill="#fff"/></svg></div>
  <div class="why-item" style="left:752px;top:333px"><b>Unmatched Personal Service</b>Lorem ipsum dolor sit amet, consectetuer adipiscing elit, sed diam.</div>
  <div class="why-icon" style="left:578px;top:400px;background:var(--blue)"><svg width="18" height="18"><circle cx="9" cy="9" r="6" fill="none" stroke="#fff" stroke-width="2"/></svg></div>
  <div class="why-item" style="left:475px;top:450px;text-align:center"><b>24/7 U.S. Based Customer Support</b>Lorem ipsum dolor sit amet, consectetuer adipiscing elit, sed diam.</div>
</section>

<section class="team">
  <h2 class="section-title" style="top:3483px">Our Team</h2>
  <p class="lead" style="top:3533px">Lorem ipsum dolor sit amet, consectetuer adipiscing elit, sed diam nonummy nibh euismod tincidunt ut laoreet dolore magna aliquam erat volutpat. Ut wisi enim ad minim veniam, quis nostrud exerci.</p>
  <span class="team-arrow" style="left:112px">‹</span>
  <div class="member" style="left:150px">
    <div class="member-photo" role="img" aria-label="Portrait of Daniel Ferrow"></div>
    <div class="member-head"><b>DANIEL FERROW</b><span>Chief Executive Officer</span></div>
    <p>Lorem ipsum dolor sit amet, consectetuer adipiscing elit, sed diam nonummy nibh euismod tincidunt ut laoreet dolore magna [...]</p>
  </div>
  <div class="member" style="left:620px">
    <div class="member-photo" role="img" aria-label="Portrait of Owen Castell"></div>
    <div class="member-head"><b>OWEN CASTELL</b><span>Chief Operations Officer</span></div>
    <p>Lorem ipsum dolor sit amet, consectetuer adipiscing elit, sed diam nonummy nibh euismod tincidunt ut laoreet dolore magna [...]</p>
  </div>
  <span class="team-arrow" style="left:1075px">›</span>
</section>

<section class="inquiry">
  <div class="placeholder" role="img" aria-label="Desk with laptop and coffee mug" style="left:0;top:3770px;width:470px;height:403px;background:linear-gradient(100deg,#eef0f2,#d3d7db 55%,#fff)"></div>
  <h2 class="section-title" style="top:3818px">Quick Inquiry</h2>
  <div class="field" style="left:493px;top:3888px;width:250px">First Name</div>
  <div class="field" style="left:770px;top:3888px;width:250px">Last Name</div>
  <div class="field" style="left:493px;top:3938px;width:250px">Email</div>
  <div class="field" style="left:770px;top:3938px;width:250px">Phone Number</div>
  <div class="field" style="left:493px;top:3988px;width:527px;height:90px;border:none">Details About Your Enquiry<div style="margin-top:8px;height:70px;border:1px solid #ccc"></div></div>
  <div class="submit">SUBMIT</div>
</section>

<footer class="site-footer" role="img" aria-label="Dark city skyline backdrop behind footer">
  <svg class="abs" style="left:0;top:-2px" width="1200" height="22" viewBox="0 0 1200 22"><path d="M0 0h1200v8q-100 12-200 0t-200 0-200 0-200 0-200 0-200 0z" fill="#fff"/></svg>
  <div class="foot-col" style="left:150px"><h4>Quick <span>Links</span></h4>
    <ul><li>Home</li><li>Services</li><li>Pricing</li><li>Our Team</li><li>Success Stories</li><li>Clients</li><li>Contact Us</li></ul></div>
  <div class="foot-col" style="left:345px"><h4>Contact <span>Details</span></h4>
    <b>BrightHarbor.com</b><br>Street Name, City Name<br>State Zipcode<br><br>☎ 555-014-2290<br>☎ 555-014-2291<br>✉ hello@brightharbor.com</div>
  <div class="foot-col" style="left:615px;width:240px"><h4>Newsletter <span>Signup</span></h4>
    Lorem ipsum dolor sit amet, consectetuer adipiscing elit, sed diam.
    <div class="news-input">Email</div><span class="news-btn">Subscribe</span></div>
  <div class="abs" style="left:915px;top:110px;font-family:'Tinos',serif;font-size:24px;font-weight:700;color:#fff">BrightHarbor.com</div>
</footer>
<div class="copyright"><span>Copyright © 2017 BrightHarbor.com. All rights reserved.</span><span>Terms of Use | Privacy Policy</span></div>

</body>
</html>
```